New web/graphic designs required to improve existing ecommerce site.

Initial outline of project:
This project is for new designs to fit into areas of existing webpages - specifically:-
Objective 1 - Produce 8 home page design proposals (design for central area of page only, not whole page)
Objective 2 - Produce 5 designs for page header banners (950px x 84px images)
Objective 3 - Produce 10 designs for help guide covers (316px x 410px images)
Also, on a more general note:
Objective 4 - Review and suggest improvements for other areas website. (This may lead to further design work)
-
Introduction to the Periodical Bazaar website:
The Periodical Bazaar website is a marketplace where back-issue hobby magazines can be bought and sold, and in some cases downloaded & viewed in digital form. The ‘sellers’ of the magazines will be both traders and private individuals. Trade sellers will also be able to sell magazine subscriptions and have ‘Promotion Pages’ about themselves and/or their magazine titles on the site. Other forms of advertising will also be available on the site for any commercial advertisers who want it, particularly for companies supplying the various hobbies covered.
Users of the website can locate magazines of interest to them by browsing through the hobby / category sections of the site, or by doing keyword searches for issues containing articles on specific topics.
The site is split-up into sections dealing with magazines about specific hobby subjects – ie., cars, motorbikes, railway, aviation, boating etc. Although part of the larger site, each of these sections is largely self-contained, with many users only ever browsing in the section related to their hobby. As such, each section effectively has it’s own home page, which will duplicate much of the information shown on the main home page. These multiple ‘section home pages’ will be promoted in their own right via URLs specific to that hobby. Currently there are 8 sections, but this number is expected to increase as the site grows.
This website is still being developed, but is close to launch; as such the website is fully functional but a lot of content is missing - please bear this in mind when viewing the site, and feel free to ask for clarification if anything is unclear.
The new website is currently at: http://www2.periodicalbazaar.co.uk
This website will replace several existing sites:-
http://www.periodicalbazaar.co.uk
http://www.twowheel-journals.co.uk
http://www.skyward-journals.co.uk
http://www.drivepapers.co.uk
http://www.trackside-journals.co.uk
http://www.scalecraft-journals.co.uk
-
Design notes:
The overall design is fairly conventional and very much ‘functionality’ driven, the website being at it’s heart an ecommerce system with some fairly complex features. Nevertheless I want the site to appear simple and modern in appearance, being somewhere between an ‘all style’ Web 2.0-type site (eg. tintly.io), and an ‘all function’ conventional trading site (eg. Bravlo, Quibb etc). A good example of a style of site which I would like to emulate is PostGecko – a complex and large site made to look friendly and approachable by the use of simple, clear design, bold colour and a sense of humour.
To explain further what is required I have prepared various image documents which include more detailed notes on the various objectives for this project. There is a lot of information in these documents - please read them carefully:-
Objective 1:
- Produce 1 'Main Home Page' design proposal
- Produce 8 'Section Home Page' design proposals - one each for these sections: Railway, Boating, Aviation, Cycling, Automotive, Motorcycling, Men's Lifestyle, Modelling
More information on Objective 1 is given in these image documents:
http://www.filenook.net/Home_Page_Designs-Purpose.gif
http://www.filenook.net/Home_Page_Designs-Areas.gif
http://www.filenook.net/Section_Home_Pages-1.gif
http://www.filenook.net/Section_Home_Pages-2.gif
-
Objective 2:
- Produce 5 designs for page header banners (950px x 84px images)
More information on Objective 2 is given in this image document:
http://www.filenook.net/Page_Header_Banners.gif
-
Objective 3:
- Produce 10 designs for help guide covers (316px x 410px images)
http://www.filenook.net/Help_Guide_Covers.gif
-
Objective 4:
- Review and suggest improvements for other areas website
I would like the designer to spend some time looking at the whole of the current website, and suggest any areas that can be improved. I am not looking for a wholesale re-design - the overall layout of the site and major design elements such as the navigation system - are essentially fixed - however, many graphical elements can be changed, as can any text content (including text content within the navigation system).
Improvements which are suggested may lead to additional design work either as part of this project, or as subsequent projects in their own right.
-
Designers are very welcome to contact me to discuss any aspect of this project, or if more information is required about the website or the designs required.
I'm happy to guarantee this project in due course, if there is positive reaction to the project from potential designers interested in submitting designs. This is the second project I have run on ArtBrigade - the first one was successful and resulted in the Flash animation that is currently on the homepage of the website.
UPDATE 11/10/11:
I've created some new documents to illustrate the sort of designs I am looking for for the Main Home Page and Section Home Pages:
Very rough examples of the sort of style I am looking for:
http://www.filenook.net/Rough_Main_Home_Page_1.jpg
http://www.filenook.net/Rough_Main_Home_Page_2.jpg
http://www.filenook.net/Rough_Main_Home_Page_3.jpg
http://www.filenook.net/Rough_Main_Home_Page_4.jpg
http://www.filenook.net/Rough_Main_Home_Page_5.jpg
http://www.filenook.net/Rough_Section_Home_Page.jpg
http://www.filenook.net/Rough_Section_Home_Page_2.jpg
Detailed document showing exact content required for the Main Home Page and each Section Home Page:
http://www.filenook.net/Home_Page_Content.gif
Target Market(s)
Mainly male, age 20 - 60. Not necessarily 'web savvy' or design-conscious
Industry/Entity Type
Advertising
Look and feel

```html
<!DOCTYPE html>
<html lang="en">
<head>
<meta charset="utf-8">
<title>Page Header Banners – Periodical Bazaar</title>
<link rel="stylesheet" href="https://fonts.googleapis.com/css2?family=Poppins:wght@700&family=Questrial&family=Arimo:wght@400;700&display=swap">
<style>
  :root {
    --page-bg: #ffffff;
    --ink: #111111;
    --bubble: #ffffff;
    --link: #1a5fd0;
    --checkout-top: #7d0a02; --checkout-mid: #e8200c; --checkout-low: #c01005;
    --login-top: #0b8c9c; --login-mid: #22dcec; --login-low: #10b8c8;
    --help-top: #0a5e92; --help-mid: #1ca6e6; --help-low: #0e86c6;
    --search-top: #7e8c00; --search-mid: #d6ee00; --search-low: #b4cc00;
    --mags-top: #8c6e00; --mags-mid: #f2cc00; --mags-low: #cfa800;
    --figure-a: #c9d3da;
    --figure-b: #e9d2b6;
    --plus-green: #3aa83a;
  }
  * { margin: 0; padding: 0; box-sizing: border-box; }
  html, body { width: 1200px; height: 748px; overflow: hidden; background: var(--page-bg); }
  .stage {
    position: relative; width: 1050px; height: 654px;
    transform: scale(1.142857); transform-origin: 0 0;
  }
  .banner {
    position: absolute; left: 51px; width: 950px; height: 84px;
    border-radius: 6px; overflow: hidden;
  }
  .banner--checkout { top: 39px;  background: linear-gradient(180deg, var(--checkout-top), var(--checkout-mid) 55%, var(--checkout-low)); }
  .banner--login    { top: 163px; background: linear-gradient(180deg, var(--login-top), var(--login-mid) 55%, var(--login-low)); }
  .banner--help     { top: 288px; background: linear-gradient(180deg, var(--help-top), var(--help-mid) 55%, var(--help-low)); }
  .banner--search   { top: 412px; background: linear-gradient(180deg, var(--search-top), var(--search-mid) 55%, var(--search-low)); }
  .banner--mags     { top: 536px; background: linear-gradient(180deg, var(--mags-top), var(--mags-mid) 55%, var(--mags-low)); }
  .banner__icon { position: absolute; border-radius: 6px; }
  .banner__title {
    position: absolute; top: 22px;
    font-family: "Poppins", sans-serif; font-weight: 700; font-size: 31px;
    letter-spacing: 0.5px; color: var(--ink); line-height: 1;
    -webkit-box-reflect: below -4px linear-gradient(transparent 55%, rgba(0,0,0,0.25));
  }
  .banner__figure {
    position: absolute; top: 2px; width: 86px; height: 82px;
    border-radius: 10px 10px 0 0;
    background: linear-gradient(160deg, var(--figure-a), var(--figure-b));
  }
  .banner__bubble {
    position: absolute; top: 8px; height: 69px; background: var(--bubble);
    border-radius: 8px; padding: 0 20px;
    display: flex; flex-direction: column; justify-content: center;
  }
  .bubble__lorem {
    font-family: "Questrial", sans-serif; font-size: 11px; line-height: 14px;
    letter-spacing: 0.45px; white-space: nowrap; color: var(--ink);
  }
  .bubble__heading { font-family: "Arimo", sans-serif; font-weight: 700; font-size: 11px; color: var(--ink); margin-bottom: 3px; white-space: nowrap; }
  .bubble__text { font-family: "Arimo", sans-serif; font-size: 12px; color: var(--ink); line-height: 19px; white-space: nowrap; }
  .bubble__link { color: var(--link); }
</style>
</head>
<body>
<div class="stage">

  <section class="banner banner--checkout">
    <div class="banner__icon" style="left:17px;top:9px;width:72px;height:62px;background:linear-gradient(180deg,#d8d8d8,#9a9a9a 70%,#d4a640);" role="img" aria-label="Cash register with coins icon"></div>
    <h2 class="banner__title" style="left:99px;">CHECKOUT</h2>
    <div class="banner__figure" style="left:369px;" role="img" aria-label="Mascot figure holding up the message sign"></div>
    <div class="banner__bubble" style="left:454px;width:408px;">
      <p class="bubble__lorem">Lorem ipsum dolor sit amet, consectetur adipisicing elit, sed<br>do eiusmod tempor incididunt ut labore et dolore magna<br>aliqua. Ut enim ad minim veniam, quis nostrud exercitation</p>
    </div>
  </section>

  <section class="banner banner--login">
    <div class="banner__icon" style="left:15px;top:12px;width:66px;height:60px;background:linear-gradient(180deg,#f4f4f4,#cfd6da);" role="img" aria-label="Form sheet and pencil icon"></div>
    <h2 class="banner__title" style="left:100px;">LOGIN - REGISTER</h2>
    <div class="banner__figure" style="left:440px;" role="img" aria-label="Mascot figure holding up the message sign"></div>
    <div class="banner__bubble" style="left:526px;width:353px;">
      <p class="bubble__heading">WELCOME, NEW USER</p>
      <p class="bubble__text">Simply fill in your details below to create your account!</p>
    </div>
  </section>

  <section class="banner banner--help">
    <svg class="banner__icon" style="left:36px;top:17px;" width="52" height="52" viewBox="0 0 52 52" aria-hidden="true">
      <circle cx="26" cy="26" r="25" fill="var(--plus-green)"/>
      <circle cx="26" cy="26" r="25" fill="none" stroke="#1f6e1f" stroke-width="1"/>
      <path d="M21 12h10v9h9v10h-9v9H21v-9h-9V21h9z" fill="#ffffff"/>
    </svg>
    <h2 class="banner__title" style="left:121px;">HELP CENTER</h2>
    <div class="banner__figure" style="left:413px;" role="img" aria-label="Mascot figure holding up the message sign"></div>
    <div class="banner__bubble" style="left:499px;width:408px;padding-left:25px;">
      <p class="bubble__heading">WELCOME TO HELP CENTER,</p>
      <p class="bubble__text">If your question isnt listed belove, please be free to contact us<br><span class="bubble__link">support@periodicalbazaar.com</span></p>
    </div>
  </section>

  <section class="banner banner--search">
    <div class="banner__icon" style="left:19px;top:12px;width:95px;height:66px;background:linear-gradient(180deg,#dfe6ea,#8aa0ac 60%,#5b7c8a);" role="img" aria-label="Car under a magnifying glass icon"></div>
    <h2 class="banner__title" style="left:148px;">SEARCH</h2>
    <div class="banner__figure" style="left:369px;" role="img" aria-label="Mascot figure holding up the message sign"></div>
    <div class="banner__bubble" style="left:454px;width:408px;">
      <p class="bubble__lorem">Lorem ipsum dolor sit amet, consectetur adipisicing elit, sed<br>do eiusmod tempor incididunt ut labore et dolore magna<br>aliqua. Ut enim ad minim veniam, quis nostrud exercitation</p>
    </div>
  </section>

  <section class="banner banner--mags">
    <div class="banner__icon" style="left:15px;top:8px;width:129px;height:72px;background:linear-gradient(180deg,#e6e6e6,#9a9a9a);" role="img" aria-label="Open magazines with a padlock icon"></div>
    <h2 class="banner__title" style="left:154px;">MY MAGS</h2>
    <div class="banner__figure" style="left:369px;" role="img" aria-label="Mascot figure holding up the message sign"></div>
    <div class="banner__bubble" style="left:454px;width:408px;">
      <p class="bubble__lorem">Lorem ipsum dolor sit amet, consectetur adipisicing elit, sed<br>do eiusmod tempor incididunt ut labore et dolore magna<br>aliqua. Ut enim ad minim veniam, quis nostrud exercitation</p>
    </div>
  </section>

</div>
</body>
</html>
```